Senior Benefits checkup postcard

develop oversize postcard for direct mail campaign for senior market insurance agency. Targeting seniors ages 50-80. offering a no cost or free benefits checkup for Life, Health and wealth protection.. Posing questions to seniors Such as. *With over 280 insurance companies in our state, How do you find the right plan?* Can I save money on my vantora plan? Who covers my illnesses? Is my life insurance policy still good? Who has the best smoker rates? Who covers diabetes or COPD with no waiting period? many questions senior can ask themselves, be open.
Prompt clients to call local phone number to schedule their free benefits check up. A state licensed agent will consult seniors in the privacy of their own home. Welcome their children or caregivers to attend.
Updates

Thank you designers for all your hard work and efforts. You have given us many options to chose form and things to discuss.I appreciate your input and suggestions. Keep up the great work you do.

Target Market(s)

Seniors ages 50-80, Life, Health, Vantora, and wealth protection. This is for consumers not agents.

Industry/Entity Type

Insurance

Font styles to use
Sans Serif

Requirements
Must have
• Phone number to call in. Company logo, area for mailing label.and postage.
Nice to have
• Use both sides to market program, photos of seniors. easy to read for older seniors. List of product offering.using attachments listed as business card back.
Should not have
• Cannot use words such as Best, cheapest, lowest, etc
• due to vantora advertising guidelines.

```html
<!DOCTYPE html>
<html lang="en">
<head>
<meta charset="utf-8">
<title>Silver Oak Benefits Group – Benefits Checkup Postcard</title>
<link rel="stylesheet" href="https://fonts.googleapis.com/css2?family=Tinos:ital,wght@0,400;0,700;1,700&display=swap">
<style>
  :root {
    --navy: #1b3a6b;
    --red: #d7191f;
    --white: #ffffff;
    --sky-top: #b9cde6;
    --sky-mid: #d6e3f1;
    --sky-low: #e6edf5;
    --band: rgba(255, 255, 255, 0.62);
    --photo-cream: #efe6d2;
    --photo-warm: #d9a878;
    --photo-autumn: #c9814a;
    --photo-green: #4f9a55;
  }
  * { margin: 0; padding: 0; box-sizing: border-box; }
  html, body { width: 1200px; height: 682px; overflow: hidden; background: var(--white); }
  .postcard {
    position: relative;
    width: 1200px;
    height: 682px;
    overflow: hidden;
    background: linear-gradient(180deg, var(--sky-top) 0%, var(--sky-mid) 55%, var(--sky-low) 100%);
    font-family: "Tinos", "Times New Roman", serif;
  }
  .photo-area {
    position: absolute;
    left: 0; top: 0;
    width: 640px; height: 682px;
    background:
      linear-gradient(90deg, rgba(255,255,255,0) 70%, var(--sky-mid) 100%),
      radial-gradient(ellipse at 70% 85%, var(--photo-green) 0%, rgba(79,154,85,0) 35%),
      radial-gradient(ellipse at 35% 45%, var(--photo-warm) 0%, rgba(217,168,120,0) 45%),
      radial-gradient(ellipse at 10% 20%, var(--photo-autumn) 0%, rgba(201,129,74,0) 40%),
      linear-gradient(180deg, #e3c9a8 0%, var(--photo-cream) 60%, #e9e4da 100%);
  }
  .photo-edge {
    position: absolute;
    left: 0; top: 0;
    width: 96px; height: 682px;
    background: linear-gradient(90deg, rgba(255,255,255,0.85), rgba(255,255,255,0.2));
  }
  .headline {
    position: absolute;
    right: 56px; top: 26px;
    text-align: right;
    color: var(--white);
    font-style: italic;
    font-weight: 700;
    font-size: 44px;
    line-height: 62px;
    text-shadow: 0 1px 3px rgba(27,58,107,0.25);
  }
  .headline .figure { color: var(--red); font-size: 64px; }
  .headline .accent { color: var(--red); }
  .web-address {
    position: absolute;
    right: 44px; top: 388px;
    color: var(--red);
    font-size: 15px;
  }
  .contact-band {
    position: absolute;
    left: 0; top: 425px;
    width: 1156px; height: 225px;
    background: var(--band);
  }
  .call-label {
    position: absolute;
    left: 250px; top: 490px;
    width: 210px;
    text-align: center;
    color: var(--navy);
    font-weight: 700;
    font-size: 40px;
  }
  .phone {
    position: absolute;
    left: 72px; top: 548px;
    display: flex;
    align-items: center;
    gap: 14px;
    color: var(--navy);
    font-weight: 700;
    font-size: 62px;
    line-height: 1;
  }
  .phone-icon { width: 82px; height: 82px; }
  .brand {
    position: absolute;
    right: 56px; top: 500px;
    color: var(--navy);
    text-align: right;
  }
  .brand-lockup { display: flex; align-items: center; justify-content: flex-end; gap: 14px; }
  .brand-dot {
    width: 34px; height: 34px;
    border-radius: 50%;
    background: var(--navy);
    flex: none;
  }
  .brand-name {
    font-size: 34px;
    font-weight: 700;
    line-height: 1.1;
    white-space: nowrap;
  }
  .brand-tagline {
    margin-top: 16px;
    font-size: 20px;
    white-space: nowrap;
  }
</style>
</head>
<body>
<main class="postcard">
  <div class="photo-area" role="img" aria-label="Photo of a smiling senior couple outdoors in autumn, the woman riding piggyback on the man who wears a green scarf"></div>
  <div class="photo-edge"></div>

  <h1 class="headline">
    With over <span class="figure">280</span> insurance companies<br>
    in our state, how do I<br>
    find the right plan<br>
    <span class="accent">for me?</span>
  </h1>

  <p class="web-address">http://silveroakbenefits.net/</p>

  <div class="contact-band"></div>

  <p class="call-label">Call Us</p>
  <p class="phone">
    <svg class="phone-icon" viewBox="0 0 82 82" aria-hidden="true">
      <circle cx="41" cy="41" r="37" fill="none" stroke="var(--navy)" stroke-width="5"/>
      <path d="M27 22c2-2 5-2 6 0l5 8c1 2 0 4-1 5l-3 3c2 5 6 9 11 11l3-3c1-1 3-2 5-1l8 5c2 1 2 4 0 6l-4 4c-3 3-9 3-16-1-9-5-15-11-19-19-4-7-4-13-1-16z" fill="var(--navy)"/>
      <path d="M46 22a14 14 0 0 1 14 14M46 14a22 22 0 0 1 22 22" fill="none" stroke="var(--navy)" stroke-width="4" stroke-linecap="round"/>
    </svg>
    <span>803-555-0142</span>
  </p>

  <div class="brand">
    <div class="brand-lockup">
      <span class="brand-dot"></span>
      <p class="brand-name">Silver Oak Benefits Group</p>
    </div>
    <p class="brand-tagline">Life, Health and Wealth Protection</p>
  </div>
</main>
</body>
</html>
```